Awesome Business Card Design needed!

Hey there.
I'm looking for a simple but awesome business card design.
Type of company: Online advertisement agency
(please don't use the typical business people or statistics images on the card)
The front has to display the business name
and possibly some sort of logo ( perhaps something with the two M's of the biz name )
And the back of the card should say:
Name
Phone
Email
Let your imagination flow.
here are some designs that I like and that you can use as inspiration.
Simple but Awesome
http://images.lumavexo.com/designs/55128_877673_43091_thumbnail.jpg
http://images.lumavexo.com/designs/37714_747642_40106_image.jpg
http://images.lumavexo.com/designs/55128_877673_43091_image.jpg
http://images.lumavexo.com/designs/51321_781878_43091_image.jpg
http://images.lumavexo.com/designs/33378_399063_15912_image.jpg
http://images.lumavexo.com/designs/2337_271604_9495_image.jpg
good luck

```html
<!DOCTYPE html>
<html lang="en">
<head>
<meta charset="UTF-8">
<title>Corvane Media – Business Card</title>
<link rel="stylesheet" href="https://fonts.googleapis.com/css2?family=Raleway:wght@300&family=Open+Sans:wght@400;600&display=swap">
<style>
  :root {
    --stage: #e6e8ea;
    --card-dark: #0b0a0a;
    --card-dark-curve: #1c1818;
    --card-light: #ffffff;
    --gold: #c9a061;
    --gold-deep: #a77d3e;
    --chip: #f1e4dc;
    --ink: #111111;
    --ink-soft: #222222;
    --glow-warm: #f6dc9a;
    --glow-cool: #a9d3d2;
  }
  * { margin: 0; padding: 0; box-sizing: border-box; }
  html, body { width: 1200px; height: 621px; overflow: hidden; }
  body { background: var(--stage); position: relative; }

  .card {
    position: absolute;
    top: 268px;
    width: 488px;
    height: 282px;
    border-radius: 30px;
    overflow: hidden;
  }

  /* Front */
  .card--front { left: 75px; background: var(--card-dark); }
  .card__curves { position: absolute; inset: 0; }
  .front__bar {
    position: absolute; left: 0; top: 130px;
    width: 65px; height: 23px;
    background: linear-gradient(90deg, var(--gold-deep), var(--gold));
  }
  .front__chip {
    position: absolute; left: 66px; top: 130px;
    width: 17px; height: 23px; background: var(--chip);
  }
  .front__name {
    position: absolute; left: 88px; top: 124px;
    font-family: "Raleway", sans-serif; font-weight: 300;
    font-size: 31px; letter-spacing: 2px; color: var(--gold);
    white-space: nowrap;
  }
  .front__circle {
    position: absolute; left: 389px; top: 88px;
    width: 84px; height: 84px; border-radius: 50%;
    border: 2px solid var(--gold);
  }

  /* Back */
  .card--back {
    left: 641px;
    background:
      radial-gradient(ellipse 70% 55% at 100% 100%, var(--glow-warm) 0%, rgba(246,220,154,0.35) 45%, rgba(255,255,255,0) 75%),
      radial-gradient(ellipse 55% 25% at 45% 100%, var(--glow-cool) 0%, rgba(169,211,210,0) 80%),
      var(--card-light);
  }
  .back__circle {
    position: absolute; left: 27px; top: 28px;
    width: 90px; height: 90px; border-radius: 50%;
    background: var(--ink);
  }
  .back__name {
    position: absolute; left: 127px; top: 50px;
    font-family: "Raleway", sans-serif; font-weight: 300;
    font-size: 31px; letter-spacing: 2px; color: var(--ink);
    white-space: nowrap;
  }
  .back__tagline {
    position: absolute; left: 128px; top: 84px;
    font-family: "Open Sans", sans-serif; font-weight: 400;
    font-size: 16px; letter-spacing: 1px; color: var(--ink);
  }
  .contact { position: absolute; left: 106px; top: 158px; list-style: none; }
  .contact__row {
    display: flex; align-items: center; height: 27px;
    font-family: "Open Sans", sans-serif; font-size: 14px;
    letter-spacing: 1px; color: var(--ink-soft);
  }
  .contact__icon {
    width: 26px; margin-right: 29px; display: flex; justify-content: center;
    font-weight: 600; font-size: 15px; color: var(--ink);
  }
</style>
</head>
<body>

  <section class="card card--front" aria-label="Card front">
    <svg class="card__curves" viewBox="0 0 488 282" aria-hidden="true">
      <path d="M0 95 C140 60 300 130 488 105 L488 282 L0 282 Z" fill="var(--card-dark-curve)" opacity="0.55"/>
      <path d="M0 200 C160 170 320 230 488 190 L488 282 L0 282 Z" fill="#000" opacity="0.6"/>
      <path d="M330 0 C420 40 470 90 488 140 L488 0 Z" fill="var(--card-dark-curve)" opacity="0.5"/>
    </svg>
    <div class="front__bar"></div>
    <div class="front__chip"></div>
    <div class="front__name">CORVANE Media</div>
    <div class="front__circle"></div>
  </section>

  <section class="card card--back" aria-label="Card back">
    <div class="back__circle"></div>
    <div class="back__name">CORVANE Media</div>
    <div class="back__tagline">Online advertisement agency</div>
    <ul class="contact">
      <li class="contact__row"><span class="contact__icon">N.</span>Corvane Media</li>
      <li class="contact__row">
        <span class="contact__icon">
          <svg width="22" height="20" viewBox="0 0 24 22" aria-hidden="true">
            <path d="M3 8 C3 4 7 2 12 2 C17 2 21 4 21 8 L17 9 L16 6 C13 5 11 5 8 6 L7 9 Z" fill="var(--ink)" transform="rotate(-30 12 11)"/>
          </svg>
        </span>(054) 555 0142
      </li>
      <li class="contact__row">
        <span class="contact__icon">
          <svg width="22" height="20" viewBox="0 0 24 22" aria-hidden="true">
            <path d="M3 8 L12 2 L21 8 L21 20 L3 20 Z M3 8 L12 14 L21 8" fill="none" stroke="var(--ink)" stroke-width="1.6" stroke-linejoin="round"/>
          </svg>
        </span>corvanemedia@mailbox.com
      </li>
    </ul>
  </section>

</body>
</html>
```